The Linen Loft Co

We need a business card design for our wardrobe company.
Please visit our website www.gentlelinenlofts.com to get an idea of who we are.

```html
<!DOCTYPE html>
<html lang="en">
<head>
<meta charset="utf-8">
<title>The Linen Loft Co – Business Card</title>
<link href="https://fonts.googleapis.com/css2?family=Roboto:wght@400;500;700&display=swap" rel="stylesheet">
<style>
  :root {
    --backdrop: #e9e7e3;
    --card: #ffffff;
    --ink: #111111;
    --muted: #9a9a9a;
    --body: #555555;
    --rule: #cfcfcf;
    --band: #0b0b0b;
    --strip-light: #d8d8d8;
    --strip-dark: #9d9d9d;
  }
  * { margin: 0; padding: 0; box-sizing: border-box; }
  html, body {
    width: 1200px; height: 801px; overflow: hidden;
    background: var(--backdrop);
    font-family: "Roboto", Arial, sans-serif;
  }
  .card {
    position: absolute; left: 100px; top: 115px;
    width: 1000px; height: 571px;
    background: var(--card);
    box-shadow: 0 10px 30px rgba(0,0,0,0.18);
    overflow: hidden;
  }
  .brand {
    position: absolute; left: 600px; top: 150px;
    display: flex; align-items: center; gap: 18px;
  }
  .brand-square { width: 22px; height: 22px; background: var(--ink); }
  .brand-name {
    font-size: 28px; font-weight: 700; color: var(--ink);
    text-transform: uppercase; letter-spacing: 0.5px;
  }
  .brand-tagline {
    position: absolute; left: 640px; top: 196px;
    font-size: 22px; font-weight: 700; color: var(--ink);
  }
  .person { position: absolute; left: 75px; top: 205px; }
  .person-name { font-size: 42px; font-weight: 700; color: var(--ink); line-height: 1.1; }
  .person-role { font-size: 24px; color: var(--muted); margin-top: 2px; }
  .contacts { position: absolute; left: 75px; top: 320px; }
  .contact-row {
    display: flex; align-items: center; gap: 16px;
    font-size: 24px; color: var(--body); line-height: 38px;
  }
  .contact-row svg { width: 20px; height: 20px; fill: var(--ink); }
  .rule {
    position: absolute; left: 75px; right: 75px; top: 412px;
    height: 2px; background: var(--rule);
  }
  .address {
    position: absolute; right: 75px; top: 428px;
    text-align: right; font-size: 24px; line-height: 30px; color: var(--body);
  }
  .footer { position: absolute; left: 0; bottom: 0; width: 1000px; height: 60px; }
  .website {
    position: absolute; right: 40px; bottom: 12px;
    font-size: 26px; color: #ffffff; letter-spacing: 0.3px;
  }
</style>
</head>
<body>
  <div class="card">
    <div class="brand">
      <span class="brand-square"></span>
      <span class="brand-name">The Linen Loft Co</span>
    </div>
    <div class="brand-tagline">Crafted for Every Room</div>

    <div class="person">
      <div class="person-name">Daniel Hartley</div>
      <div class="person-role">President</div>
    </div>

    <div class="contacts">
      <div class="contact-row">
        <svg viewBox="0 0 24 24" aria-hidden="true"><path d="M6.6 10.8a15 15 0 0 0 6.6 6.6l2.2-2.2c.3-.3.7-.4 1-.2 1.1.4 2.3.6 3.6.6.6 0 1 .4 1 1V20c0 .6-.4 1-1 1A17 17 0 0 1 3 4c0-.6.4-1 1-1h3.5c.6 0 1 .4 1 1 0 1.3.2 2.5.6 3.6.1.3 0 .7-.2 1z"/></svg>
        <span>020 7946 0318</span>
      </div>
      <div class="contact-row">
        <svg viewBox="0 0 24 24" aria-hidden="true"><path d="M2 5h20v2l-10 6L2 7zM2 9l10 6 10-6v10H2z"/></svg>
        <span>info@gentlelinenlofts.com</span>
      </div>
    </div>

    <div class="rule"></div>

    <div class="address">
      Harbour House, 48 Mill Lane<br>
      London N4 3QT
    </div>

    <svg class="footer" viewBox="0 0 1000 60" preserveAspectRatio="none" aria-hidden="true">
      <defs>
        <linearGradient id="stripShade" x1="0" y1="0" x2="0" y2="1">
          <stop offset="0" stop-color="#d8d8d8"/>
          <stop offset="1" stop-color="#9d9d9d"/>
        </linearGradient>
      </defs>
      <path d="M0 30 L420 30 Q440 30 445 45 L450 60 L0 60 Z" fill="url(#stripShade)"/>
      <path d="M410 60 Q425 10 460 8 L1000 8 L1000 60 Z" fill="#0b0b0b"/>
    </svg>
    <div class="website">www.gentlelinenlofts.com</div>
  </div>
</body>
</html>
```